Local business providing residential house cleaning services

We need a business card design that is "cute" or "cartoonish" while still maintaining a professional appeal. Tidal Sweepers is the name. We would like to use a "pin up girl" or maid next to the name with a broom or vacuum cleaner. We want the look to have a 50's American look to it. We are not sure if we want the pin up girl in a maid outfit or with a broom or vacuum cleaner but we hope some of you will be able to take these ideas and be creative. If you have any questions at all please don't hesitate to message me so that we can get the best design possible. Thank you very much and I look forward to seeing some designs! Mira Hollister

Target Market(s)

Upper class Americans that are busy and have money and want to come home to a clean house.

Industry/Entity Type

Cleaning Service

Contact Information for Business Card

Pin up girl incorporated into the card is a must.

Font styles to use
Decorative
Script

Requirements
Must have
• Pin up girl
Nice to have
• A crown used on the Q possibly.

```html
<!DOCTYPE html>
<html lang="en">
<head>
<meta charset="utf-8">
<title>Tidal Sweepers – Business Card</title>
<link rel="stylesheet" href="https://fonts.googleapis.com/css2?family=Libre+Baskerville:ital,wght@0,400;0,700;1,400&display=swap">
<style>
  :root {
    --page-bg: #f1f1f1;
    --card-pink: #ef8fa0;
    --card-pink-light: #f3a5b3;
    --frame-pink: #e8667f;
    --frame-line: #f6c3cd;
    --panel-white: #ffffff;
    --ink: #2b2b2b;
    --brand-pink: #e8667f;
    --figure-soft: #f6dde3;
    --figure-softer: #fbeef1;
  }
  * { margin: 0; padding: 0; box-sizing: border-box; }
  html, body {
    width: 1200px;
    height: 811px;
    overflow: hidden;
    background: var(--page-bg);
  }
  .business-card {
    position: absolute;
    left: 185px;
    top: 175px;
    width: 819px;
    height: 477px;
    border-radius: 38px;
    background: radial-gradient(ellipse at 50% 50%, var(--card-pink-light) 0%, var(--card-pink) 75%);
    box-shadow: 0 6px 18px rgba(0,0,0,0.12);
    overflow: hidden;
  }
  .card-border-pattern {
    position: absolute;
    inset: 0;
  }
  .label-frame {
    position: absolute;
    left: 0;
    top: 0;
    width: 819px;
    height: 477px;
  }
  .pinup-figure {
    position: absolute;
    left: 96px;
    top: 150px;
    width: 186px;
    height: 290px;
    border-radius: 90px 90px 30px 30px;
    background: linear-gradient(180deg, var(--figure-soft) 0%, var(--figure-softer) 100%);
  }
  .brand-name {
    position: absolute;
    left: 360px;
    top: 108px;
    width: 280px;
    font-family: "Libre Baskerville", Georgia, serif;
    font-weight: 700;
    font-size: 46px;
    line-height: 1.15;
    color: var(--brand-pink);
    text-align: center;
  }
  .contact-block {
    position: absolute;
    left: 272px;
    top: 268px;
    font-family: "Libre Baskerville", Georgia, serif;
    font-style: italic;
    color: var(--ink);
  }
  .contact-name {
    font-size: 28px;
    line-height: 1;
    margin-bottom: 22px;
  }
  .contact-line {
    display: flex;
    align-items: center;
    gap: 12px;
    font-size: 22px;
    line-height: 1;
    margin-bottom: 20px;
  }
  .contact-icon {
    width: 20px;
    height: 20px;
    flex: none;
  }
</style>
</head>
<body>
  <div class="business-card">
    <div class="card-border-pattern" role="img" aria-label="Pink polka-dot pattern across the card border"></div>
    <svg class="label-frame" viewBox="0 0 819 477" aria-hidden="true">
      <path d="M112 55 L350 55 Q395 55 409 32 Q423 55 468 55 L719 55
               A40 40 0 0 0 759 95 L759 206 Q774 246 759 286 L759 397
               A40 40 0 0 0 719 437 L468 437 Q423 437 409 460 Q395 437 350 437 L112 437
               A40 40 0 0 0 72 397 L72 286 Q57 246 72 206 L72 95
               A40 40 0 0 0 112 55 Z"
            fill="#ffffff" stroke="#e8667f" stroke-width="9" stroke-linejoin="round"/>
      <path d="M116 66 L352 66 Q394 66 409 46 Q424 66 466 66 L715 66
               A34 34 0 0 0 748 99 L748 208 Q760 246 748 284 L748 393
               A34 34 0 0 0 715 426 L466 426 Q424 426 409 446 Q394 426 352 426 L116 426
               A34 34 0 0 0 83 393 L83 284 Q71 246 83 208 L83 99
               A34 34 0 0 0 116 66 Z"
            fill="none" stroke="#f6c3cd" stroke-width="2"/>
    </svg>
    <div class="pinup-figure" role="img" aria-label="Illustration of a 1950s pin-up maid in a black dress and pink polka-dot apron holding a feather duster"></div>
    <div class="brand-name">Tidal<br>Sweepers</div>
    <div class="contact-block">
      <p class="contact-name">Mira Hollister</p>
      <p class="contact-line">
        <svg class="contact-icon" viewBox="0 0 20 20" aria-hidden="true">
          <rect x="5" y="1.5" width="10" height="17" rx="2" fill="none" stroke="#e8667f" stroke-width="1.6"/>
          <line x1="8" y1="15.5" x2="12" y2="15.5" stroke="#e8667f" stroke-width="1.6"/>
        </svg>
        501-555-0142
      </p>
      <p class="contact-line">
        <svg class="contact-icon" viewBox="0 0 20 20" aria-hidden="true">
          <rect x="1.5" y="4.5" width="17" height="11" fill="none" stroke="#e8667f" stroke-width="1.6"/>
          <polyline points="1.5,4.5 10,11 18.5,4.5" fill="none" stroke="#e8667f" stroke-width="1.6"/>
        </svg>
        mira.hollister@mailbox.com
      </p>
    </div>
  </div>
</body>
</html>
```